BOLD & MINIMALIST DESIGN NEEDED

We want a very bold but minimalistic business card design that is impactful and utilizes both sides of the business card. Our current logo is included for your use.

We want bold fonts and good use of negative space. We don't want the logo to overpower the design.

Target Market(s)

Professionals who are building new commercial buildings.

Industry/Entity Type

Construction

Contact Information for Business Card

Name, Title, email, office phone, cell phone, website

Font styles to use
Serif
Sans Serif

Requirements
Must have
• Bold design!

```html
<!DOCTYPE html>
<html lang="en">
<head>
<meta charset="utf-8">
<title>Ridgemont Design + Build — Business Card</title>
<link href="https://fonts.googleapis.com/css2?family=Roboto:wght@500;700;900&display=swap" rel="stylesheet">
<style>
  :root {
    --backdrop: #dfe4e2;
    --card: #ffffff;
    --ink: #111111;
    --text-grey: #505050;
    --accent-green: #7cc242;
  }
  * { box-sizing: border-box; margin: 0; padding: 0; }
  html, body {
    width: 1200px; height: 716px; overflow: hidden;
    background: var(--backdrop);
    font-family: "Roboto", Arial, sans-serif;
  }
  .stage { position: relative; width: 1200px; height: 716px; }
  .card {
    position: absolute;
    left: 370px;
    width: 460px;
    height: 263px;
    background: var(--card);
    border-radius: 14px;
  }
  .card--front { top: 94px; }
  .card--back { top: 382px; }

  .brand {
    display: flex; align-items: center; gap: 10px;
    color: var(--ink);
    font-weight: 900;
    text-transform: uppercase;
    white-space: nowrap;
  }
  .brand__square { background: var(--accent-green); flex: none; }

  .card--front .brand {
    position: absolute; left: 50%; top: 50%;
    transform: translate(-50%, -60%);
    font-size: 28px; letter-spacing: 0.5px;
  }
  .card--front .brand__square { width: 26px; height: 26px; }

  .card--back .brand {
    position: absolute; right: 20px; top: 46px;
    font-size: 12px; gap: 6px;
  }
  .card--back .brand__square { width: 14px; height: 14px; }

  .holder { position: absolute; left: 18px; top: 14px; color: var(--text-grey); }
  .holder__name { font-size: 15px; font-weight: 700; letter-spacing: 0.2px; line-height: 18px; }
  .holder__title { font-size: 11.5px; font-weight: 700; margin-top: 3px; line-height: 14px; }

  .divider {
    position: absolute; left: 18px; top: 65px;
    width: 2px; height: 112px; background: var(--ink);
  }

  .contact {
    position: absolute; left: 18px; top: 179px;
    list-style: none;
    color: var(--text-grey);
    font-size: 12.5px; font-weight: 700; line-height: 17px;
    white-space: nowrap;
  }
</style>
</head>
<body>
<main class="stage">
  <section class="card card--front" aria-label="Card front">
    <div class="brand"><span class="brand__square"></span>Ridgemont Design + Build</div>
  </section>

  <section class="card card--back" aria-label="Card back">
    <div class="holder">
      <p class="holder__name">LORNA VETCH</p>
      <p class="holder__title">Designer</p>
    </div>
    <div class="divider"></div>
    <ul class="contact">
      <li>+555-21-40876</li>
      <li>info@ridgemontbuild.com</li>
      <li>www.ridgemontbuild.com</li>
      <li>48 Kestrel Road &nbsp;| Unit 12, P.O. 7710, Dover</li>
    </ul>
    <div class="brand"><span class="brand__square"></span>Ridgemont Design + Build</div>
  </section>
</main>
</body>
</html>
```